birchwell hollow cattle company website

we would like a home page, an about us page, a page for sires, a page for dams, A sale page where we can list progreny for sale and a contact us. on the about us page we would like there to be a family picture. on the sires page we would like to have a picture of each sire, a description beside them and a link to their online profile at northern hereford registry. on the dam page we would like to have a picture of each dam, aswell as a description beside them aswell as a link to the northern hereford registry site. would like the website to very mobile phone friendly as expecting most traffic to be on phone. we would like the website to look and feel very mich like a farm, rustic, barbed wire and other farm feels. we would also like a frozen genetics pages where we can include pictures and descriptions of the sires and dams aswell as a price for embryos and semen. we need to website to be easy to maintain so we can update pictures and information as it changes, we would like there to be a feature so that people can sign up to be on our mailing list by giving us their mailing addess and email and full name
aswell as an area where they can send us a message to contact us.

leaving for work for 3 weeks in the canadian arctic will have limited ability to use the internet

Target Market(s)

other ranchers, farmers, cattlemen,

Industry/Entity Type

farming, agriculture, cattle

Coding

Coded - Design and coding required

Requirements
Must have
• about page, contact page, sires page, dams page, SALE page.
Nice to have
• country/farm vibe, barbed wire, wood,

```html
<!DOCTYPE html>
<html lang="en">
<head>
<meta charset="utf-8">
<title>Birchwell Hollow Cattle Company</title>
<link href="https://fonts.googleapis.com/css2?family=Roboto+Slab:wght@600;700&family=Open+Sans:wght@400;600;700&display=swap" rel="stylesheet">
<style>
:root{
  --brown:#6e4420;
  --brown-text:#7a4a1f;
  --beige:#e8e0d5;
  --cream:#f3efea;
  --wood:#5e4029;
  --wood-dark:#4b311f;
  --ink:#2b2b2b;
  --footer:#22160c;
  --white:#fff;
}
*{box-sizing:border-box;margin:0;padding:0}
html,body{width:1200px;height:3992px;overflow:hidden}
body{font-family:"Open Sans",Arial,sans-serif;color:var(--ink);background:#fff;position:relative}
h1,h2,h3,h4{font-family:"Roboto Slab",Georgia,serif}
a{text-decoration:none;color:inherit}
.section{position:relative;width:1200px;overflow:hidden}
.abs{position:absolute}
.btn{display:inline-block;font-size:11px;font-weight:700;padding:0 18px;height:30px;line-height:30px;font-family:"Open Sans",Arial,sans-serif;white-space:nowrap}
.btn-solid{background:var(--brown);color:#fff}
.btn-outline{border:1px solid var(--brown);color:var(--brown);line-height:28px}
.btn-white{background:#fff;color:var(--brown)}
.section-title{font-size:32px;font-weight:700;color:var(--brown-text);text-align:center;text-transform:uppercase;letter-spacing:.3px}
.read-more{font-size:11px;font-weight:700;color:var(--brown)}
.photo{display:block}

/* hero */
.hero{height:561px;background:#1c1a18}
.hero-photo{left:0;top:0;width:1200px;height:561px;background:linear-gradient(100deg,#1b1918 0%,#232020 35%,#3a3430 55%,#5a4636 72%,#3f5a3c 80%,#2a2723 100%)}
.logo{left:112px;top:8px;color:#fff;font-family:"Roboto Slab",Georgia,serif;font-weight:700;font-size:10px;line-height:12px;text-transform:uppercase;display:flex;align-items:center;gap:6px}
.logo .mark{width:14px;height:14px;background:#fff;border-radius:50%}
.nav{right:113px;top:16px;display:flex;align-items:center;gap:30px;font-size:11.5px;color:#eee}
.nav a.active{font-weight:700;color:#fff}
.nav .btn{height:30px;line-height:30px;padding:0 19px;margin-left:2px}
.hero-card{left:112px;top:141px;width:445px;height:319px;background:var(--beige);padding:38px 28px}
.hero-card h1{font-size:37px;line-height:46px;color:var(--brown-text);text-transform:uppercase;font-weight:700}
.hero-card p{font-size:11.5px;line-height:18px;margin-top:16px;width:380px;color:#333}
.hero-card .actions{margin-top:22px;display:flex;gap:12px}

/* about */
.about{height:850px;background:var(--beige)}
.about .section-title{position:absolute;top:51px;width:100%}
.about-intro{left:250px;top:106px;width:700px;text-align:center;font-size:11.5px;line-height:16.5px;color:#444}
.about-photo{left:112px;top:231px;width:623px;height:330px;background:linear-gradient(135deg,#6d5a48 0%,#3c2e24 45%,#23201f 70%,#5e4a3a 100%)}
.programs{left:673px;top:276px;width:415px;height:239px;background:var(--wood);color:#fff;text-align:center;padding:36px 48px}
.programs h2{font-size:29px;font-weight:700}
.programs p{font-size:11px;line-height:15.5px;margin-top:14px;color:#f1e9df}
.cards3{left:112px;top:580px;display:flex;gap:19px}
.pcard{width:313px;height:212px;background:#fff;padding:20px 21px;position:relative}
.pcard svg{display:block}
.pcard h3{font-size:18px;color:var(--brown-text);margin-top:10px;font-weight:700}
.pcard p{font-size:10.5px;line-height:15px;color:#555;margin-top:6px;width:240px}
.pcard .read-more{display:block;margin-top:8px}
.pcard .cow{position:absolute;right:10px;bottom:10px;width:56px;height:32px;background:#5c3a1d;border-radius:6px}

/* featured sires */
.sires{height:558px;background:var(--cream)}
.sires .section-title{position:absolute;top:74px;width:100%}
.sire-row{left:112px;top:116px;display:flex;gap:19px}
.sire{width:313px;height:335px;background:#fff;padding:9px;text-align:center}
.sire .photo{width:295px;height:198px}
.sire h3{font-size:18px;color:var(--brown-text);margin-top:13px;font-weight:700;white-space:nowrap}
.sire p{font-size:11px;line-height:15px;color:#555;margin:6px auto 0;width:270px}
.sire .btn{margin-top:10px;height:31px;line-height:29px;padding:0 19px}
.sires .all{left:543px;top:480px}

/* available */
.available{height:228px;background:linear-gradient(180deg,#6b4a32,#5a3d28 50%,#664731);color:#fff;text-align:center}
.available h2{font-size:31px;padding-top:46px;font-weight:700}
.available p{font-size:11.5px;margin-top:10px;color:#eee}
.available .btn{margin-top:20px;height:31px;line-height:31px;padding:0 20px}

/* testimonial */
.testimonial{height:438px;background:#fff}
.video{left:112px;top:61px;width:557px;height:359px;background:linear-gradient(120deg,#5d6f86 0%,#3e4a52 30%,#8a7f73 55%,#4a423c 100%)}
.play{left:368px;top:219px;width:44px;height:44px;border-radius:50%;background:#fff}
.play::after{content:"";position:absolute;left:17px;top:13px;border-left:14px solid #222;border-top:9px solid transparent;border-bottom:9px solid transparent}
.t-panel{left:669px;top:61px;width:419px;height:359px;background:var(--cream)}
.t-card{left:623px;top:134px;width:442px;height:214px;background:#fff;box-shadow:0 2px 10px rgba(0,0,0,.08);text-align:center}
.t-card .avatar{position:absolute;left:201px;top:28px;width:40px;height:40px;border-radius:50%;background:#5a5148}
.t-card .stars{position:absolute;top:77px;width:100%;color:#f0b429;font-size:9px;letter-spacing:1px}
.t-card .quote-text{position:absolute;top:94px;left:26px;width:390px;font-size:11px;line-height:15.5px;color:#444}
.t-card .name{position:absolute;top:156px;width:100%;font-size:11px;font-weight:700;color:#333}
.t-card .role{position:absolute;top:175px;width:100%;font-size:10.5px;color:#999}
.qmark{font-family:"Roboto Slab",Georgia,serif;font-size:72px;line-height:1;color:#a58060;font-weight:700}
.arrow-btn{width:24px;height:24px;background:var(--wood-dark);color:#fff;font-size:12px;text-align:center;line-height:23px}

/* blog */
.blog{height:597px;background:#fff}
.blog .section-title{position:absolute;top:38px;width:100%}
.post-img{top:98px;width:479px;height:352px}
.post{top:375px;width:405px;height:160px;background:#fff;box-shadow:0 3px 14px rgba(0,0,0,.12);padding:16px 16px}
.post .date{font-size:11px;color:#555;display:flex;align-items:center;gap:5px}
.post h3{font-size:15.5px;line-height:19px;color:var(--brown-text);margin-top:8px;font-weight:700}
.post p{font-size:11px;line-height:15px;color:#555;margin-top:6px}
.post .read-more{display:block;margin-top:10px}

/* mailing */
.mailing{height:442px;background:linear-gradient(180deg,#6a4a32,#5c3f2a 50%,#684832);text-align:center;color:#fff}
.mailing h2{font-size:31px;padding-top:56px;font-weight:700}
.mailing .sub{font-size:11.5px;margin-top:8px;color:#eee}
.form{left:387px;top:144px;width:425px;height:224px;background:var(--cream);padding:27px 30px;text-align:left;color:#333}
.form .grid{display:grid;grid-template-columns:176px 176px;column-gap:13px;row-gap:22px}
.form label{display:block;font-size:10.5px;margin-bottom:6px}
.form .field{height:30px;border:1px solid #b79f86;background:#fff}
.form .btn{display:block;width:110px;margin:22px auto 0;text-align:center;height:31px;line-height:31px;padding:0}

/* footer */
.footer{height:318px;background:var(--footer);color:#ddd}
.f-logo{left:112px;top:48px;color:#fff;font-family:"Roboto Slab",Georgia,serif;font-weight:700;font-size:11px;line-height:13px;text-transform:uppercase;display:flex;align-items:center;gap:7px}
.f-logo .mark{width:16px;height:16px;background:#fff;border-radius:50%}
.f-about{left:112px;top:118px;width:200px;font-size:11px;line-height:15px;color:#e7e0d8}
.socials{left:112px;top:196px;display:flex;gap:7px}
.socials span{width:19px;height:19px;border-radius:50%;background:#fff;display:block}
.f-col{top:52px;font-size:11px;color:#ddd}
.f-col h4{font-size:15px;color:#fff;margin-bottom:14px;font-weight:600}
.f-col li{list-style:none;line-height:21px}
.f-col .contact{display:flex;align-items:center;gap:9px;line-height:28px}
.f-rule{left:112px;top:232px;width:976px;height:1px;background:#6d5a49}
.copy{top:256px;width:100%;text-align:center;font-size:11px;color:#ddd}
</style>
</head>
<body>

<header class="section hero">
  <div class="abs hero-photo photo" role="img" aria-label="Young woman reaching over a green-railed fence to pet a black Angus cow"></div>
  <a class="abs logo" href="#"><span class="mark"></span><span>Birchwell Hollow<br>Cattle Company</span></a>
  <nav class="abs nav">
    <a class="active" href="#">Home</a>
    <a href="#">About Us</a>
    <a href="#">Sires</a>
    <a href="#">Dams</a>
    <a href="#">Sale</a>
    <a href="#">Frozen Genetics</a>
    <a href="#">Contact</a>
    <a class="btn btn-white" href="#">Contact Us Today</a>
  </nav>
  <div class="abs hero-card">
    <h1>Proven Genetics.<br>Trusted on the<br>Ranch.</h1>
    <p>Carefully selected sires and dams delivering consistent performance and superior traits.</p>
    <div class="actions">
      <a class="btn btn-solid" href="#">View Sires</a>
      <a class="btn btn-outline" href="#">View Sale Cattle</a>
    </div>
  </div>
</header>

<section class="section about">
  <h2 class="section-title">About Us</h2>
  <p class="abs about-intro">Birchwell Hollow Angus is a family-run ranch dedicated to raising top-quality Angus cattle with strong genetics, sound structure, and proven maternal traits. For generations, we have carefully selected sires and dams to ensure consistent performance, healthy offspring, and lasting herd improvement, offering elite sires, dependable dams, and frozen genetics to help ranchers strengthen their herds while maintaining the values and traditions of a family-run operation.</p>
  <div class="abs about-photo photo" role="img" aria-label="Rancher in a plaid shirt crouching beside black and white cattle at a feed bunk"></div>
  <div class="abs programs">
    <h2>OUR PROGRAMS</h2>
    <p>Our program is built on the foundation of functional, sound Angus cattle developed for real-world ranching conditions. We place a strong emphasis on fertility, structural integrity, maternal strength, and consistent performance, using proven genetics we trust in our own herd. Every breeding decision is made with the long-term success of our cattle and our customers in mind.</p>
  </div>
  <div class="abs cards3">
    <div class="pcard">
      <svg width="44" height="50" viewBox="0 0 44 50" fill="none" stroke="#6e4420" stroke-width="1.6"><circle cx="24" cy="14" r="10"/><path d="M24 8l2 4 4 .5-3 3 .8 4-3.8-2-3.8 2 .8-4-3-3 4-.5z"/><path d="M19 23l-3 9 5-2 3 4 2-9"/><path d="M2 40h8l8 3h10l10-6c2-1 4 1 2 3l-10 7H16l-6-2H2"/></svg>
      <h3>Proven Sires</h3>
      <p>Carefully selected Angus sires with proven pedigrees, strong performance data, and the consistency needed to improve the next generation.</p>
      <a class="read-more" href="#">Read More &rarr;</a>
      <div class="cow" role="img" aria-label="Small bull silhouette"></div>
    </div>
    <div class="pcard">
      <svg width="58" height="50" viewBox="0 0 58 50" fill="none" stroke="#6e4420" stroke-width="1.6"><path d="M3 8h52M5 3h48v5M8 8v30M14 8v30M22 8v30M28 8v30M36 8v30M42 8v30M50 8v30"/><path d="M2 42q7-4 14 0t14 0 14 0 12 0M2 47q7-4 14 0t14 0 14 0 12 0"/></svg>
      <h3>Strong Dams</h3>
      <p>Proven and dependable, our females bring temperament, fertility, and resilience to the herd, ensuring generations of strong, productive cattle.</p>
      <a class="read-more" href="#">Read More &rarr;</a>
      <div class="cow" role="img" aria-label="Small cow silhouette"></div>
    </div>
    <div class="pcard">
      <svg width="56" height="50" viewBox="0 0 56 50" fill="none" stroke="#6e4420" stroke-width="1.6"><path d="M6 46C20 40 14 22 28 16S42 6 50 2"/><path d="M14 48C26 40 22 28 34 22S46 12 52 8"/><path d="M12 40l7 3M16 32l8 2M22 24l8 1M30 18l8-1M38 12l6-3"/><circle cx="48" cy="36" r="5"/><path d="M44 36h-8"/></svg>
      <h3>Frozen Genetics Available</h3>
      <p>Frozen embryos and semen from carefully evaluated sires and dams, providing ranchers with reliable, high-quality genetics to strengthen and improve their herds.</p>
      <a class="read-more" href="#">Read More &rarr;</a>
      <div class="cow" role="img" aria-label="Small cow silhouette"></div>
    </div>
  </div>
</section>

<section class="section sires">
  <h2 class="section-title">Featured Sires</h2>
  <div class="abs sire-row">
    <article class="sire">
      <div class="photo" role="img" aria-label="Young black Angus bull standing in a muddy pen" style="background:linear-gradient(135deg,#7b7a74,#3b3833 55%,#6e6d66)"></div>
      <h3>Birchwell Hollow Ridgeline 318</h3>
      <p>A balanced sire combining muscle, sound structure, and reliable performance.</p>
      <a class="btn btn-outline" href="#">View Profile</a>
    </article>
    <article class="sire">
      <div class="photo" role="img" aria-label="Red bull and black calf standing on a hill at sunset" style="background:linear-gradient(180deg,#c9c2b5,#a9987d 55%,#6e5335)"></div>
      <h3>BHC Stonewall 614K</h3>
      <p>Built for strength and longevity, delivering consistent performance on every pasture.</p>
      <a class="btn btn-outline" href="#">View Profile</a>
    </article>
    <article class="sire">
      <div class="photo" role="img" aria-label="Black Angus cow with calf in a pasture lined with trees" style="background:linear-gradient(135deg,#8d8e76,#2f2c28 50%,#5f5a48)"></div>
      <h3>BHA Heritage 905J</h3>
      <p>Carrying forward strong genetics with structure, performance, and maternal reliability.</p>
      <a class="btn btn-outline" href="#">View Profile</a>
    </article>
  </div>
  <a class="abs btn btn-solid all" href="#">View All Sires</a>
</section>

<section class="section available">
  <h2>CATTLE AVAILABLE</h2>
  <p>Current and upcoming offerings bred for performance and reliability.</p>
  <a class="btn btn-white" href="#">View Sale Page</a>
</section>

<section class="section testimonial">
  <div class="abs video photo" role="img" aria-label="Farm worker carrying a bucket along rows of dairy cattle in a barn"></div>
  <div class="abs play"></div>
  <div class="abs t-panel"></div>
  <div class="abs t-card">
    <span class="abs qmark" style="left:26px;top:12px">&ldquo;</span>
    <div class="avatar" role="img" aria-label="Reviewer portrait"></div>
    <div class="stars">&#9733;&#9733;&#9733;&#9733;&#9733;</div>
    <p class="quote-text">The dams at Birchwell Hollow are dependable, strong, and produce healthy calves year after year. Their maternal traits and temperament make a noticeable difference in our herd.</p>
    <div class="name">Wade M</div>
    <div class="role">Alberta Cattleman</div>
    <span class="abs qmark" style="right:26px;top:150px">&rdquo;</span>
  </div>
  <div class="abs arrow-btn" style="left:613px;top:229px">&#8249;</div>
  <div class="abs arrow-btn" style="left:1052px;top:229px">&#8250;</div>
</section>

<section class="section blog">
  <h2 class="section-title">Our Latest Blog</h2>
  <div class="abs post-img photo" style="left:112px;background:linear-gradient(180deg,#c9cfcf,#8e9a8c 50%,#3f4a37)" role="img" aria-label="Two farmers inspecting plants inside a greenhouse"></div>
  <div class="abs post-img photo" style="left:609px;background:linear-gradient(135deg,#d8d2c6,#8a7e6e 40%,#2a2623 70%,#7d6d5b)" role="img" aria-label="Black and white cattle feeding in a barn stall"></div>
  <article class="abs post" style="left:149px">
    <div class="date"><svg width="11" height="11" viewBox="0 0 11 11" fill="none" stroke="#555"><rect x=".5" y="1.5" width="10" height="9"/><path d="M.5 4h10M3 0v3M8 0v3"/></svg>12 February, 2026</div>
    <h3>Advances in Agricultural Technology for Modern Ranchers</h3>
    <p>How tools, software, and data-driven strategies are improving productivity and efficiency.</p>
    <a class="read-more" href="#">Read More &rarr;</a>
  </article>
  <article class="abs post" style="left:646px">
    <div class="date"><svg width="11" height="11" viewBox="0 0 11 11" fill="none" stroke="#555"><rect x=".5" y="1.5" width="10" height="9"/><path d="M.5 4h10M3 0v3M8 0v3"/></svg>21 January, 2026</div>
    <h3>Birchwell Hollow Angus Welcomes a New Generation of Sires</h3>
    <p>Carefully selected bulls with proven genetics join the herd to strengthen our breeding program and support local ranchers.</p>
    <a class="read-more" href="#">Read More &rarr;</a>
  </article>
</section>

<section class="section mailing">
  <h2>JOIN OUR MAILING LIST</h2>
  <p class="sub">Get updates on upcoming sales, genetics releases, and ranch news.</p>
  <form class="abs form">
    <div class="grid">
      <div><label>First Name</label><div class="field"></div></div>
      <div><label>Last Name</label><div class="field"></div></div>
      <div><label>Email</label><div class="field"></div></div>
      <div><label>Phone Number</label><div class="field"></div></div>
    </div>
    <a class="btn btn-solid" href="#">Sign Up Now</a>
  </form>
</section>

<footer class="section footer">
  <a class="abs f-logo" href="#"><span class="mark"></span><span>Birchwell Hollow<br>Cattle Company</span></a>
  <p class="abs f-about">Birchwell Hollow Angus – Family-run ranch raising top-quality Angus cattle with strong genetics and proven performance.</p>
  <div class="abs socials"><span></span><span></span><span></span><span></span></div>
  <div class="abs f-col" style="left:423px">
    <h4>Quick Links</h4>
    <ul><li>Home</li><li>About Us</li><li>Sires</li><li>Dams</li><li>Sale</li><li>Frozen Genetics</li></ul>
  </div>
  <div class="abs f-col" style="left:615px">
    <h4>Company</h4>
    <ul><li>Terms &amp; Conditions</li><li>Privacy &amp; Policy</li><li>FAQ</li></ul>
  </div>
  <div class="abs f-col" style="left:808px">
    <h4>Contact Us</h4>
    <div class="contact"><svg width="14" height="14" viewBox="0 0 14 14"><path fill="#fff" d="M3 1l2.5 3-1.5 1.5c.8 1.8 2.2 3.2 4 4L9.5 8 13 10.5 11.5 13C6 13 1 8 1 2.5z"/></svg>+1 (555) 014-2290</div>
    <div class="contact"><svg width="14" height="14" viewBox="0 0 14 14"><circle cx="7" cy="7" r="7" fill="#fff"/><rect x="3.5" y="4.5" width="7" height="5" fill="none" stroke="#22160c"/><path d="M3.5 4.5L7 7.5l3.5-3" fill="none" stroke="#22160c"/></svg>info@birchwellhollow.com</div>
  </div>
  <div class="abs f-rule"></div>
  <p class="abs copy">© 2026 Birchwell Hollow Angus. Family-run Angus cattle operation. All rights reserved.</p>
</footer>

</body>
</html>
```